Need Business Card for our Real Estate Business with Sales Executive's Picture

PANTONE 484 C ( RED)

PANTONE 2766 C ( BLUE

Industry/Entity Type

Real Estate

Contact Information for Business Card

Name, Mobile, email, & picture of Person
Agency Phone, address, Web address

Requirements
Must have
• Our Logo Colours, Agent Picture,

```html
<!DOCTYPE html>
<html lang="en">
<head>
<meta charset="utf-8">
<title>Meridian Real Estate – Business Card</title>
<link rel="stylesheet" href="https://fonts.googleapis.com/css2?family=Work+Sans:wght@400;500;600&display=swap">
<style>
  :root {
    --page-bg: #d8d2ca;
    --card-bg: #eeebe6;
    --navy: #1f2a44;
    --navy-soft: #2c3756;
    --red: #9b2a2a;
    --ink: #2a2f3d;
    --band-text: #e6e1d6;
  }
  * { margin: 0; padding: 0; box-sizing: border-box; }
  html, body {
    width: 1200px; height: 1047px; overflow: hidden;
    background: var(--page-bg);
    font-family: "Work Sans", Arial, sans-serif;
  }
  .card {
    position: absolute; left: 80px; top: 241px;
    width: 1040px; height: 565px;
    background: var(--card-bg);
    border-radius: 22px;
    overflow: hidden;
    box-shadow: 0 18px 40px rgba(40, 30, 20, 0.18);
  }
  .agent-photo {
    position: absolute; left: 0; top: 24px;
    width: 440px; height: 488px;
    background: linear-gradient(180deg, #c9b6a4 0%, #a88a74 35%, #34406a 62%, #1e2a4c 100%);
  }
  .brand {
    position: absolute; right: 58px; top: 150px;
    width: 330px;
    display: flex; align-items: center; justify-content: center; gap: 12px;
    color: var(--navy);
    font-size: 27px; font-weight: 500; letter-spacing: 2px;
    text-transform: uppercase;
  }
  .brand-mark {
    width: 14px; height: 14px; background: var(--red);
  }
  .person {
    position: absolute; right: 58px; top: 296px; text-align: right;
  }
  .person-name {
    font-size: 36px; font-weight: 600; color: var(--navy); letter-spacing: 0.5px;
    line-height: 40px;
  }
  .person-role {
    font-size: 24px; font-weight: 400; color: var(--ink); letter-spacing: 0.5px;
    margin-top: 2px;
  }
  .contacts {
    position: absolute; right: 56px; top: 383px;
    list-style: none; text-align: right;
  }
  .contacts li {
    display: flex; justify-content: flex-end; align-items: center;
    height: 30px;
    font-size: 21px; color: var(--ink); letter-spacing: 0.6px;
  }
  .contacts svg { width: 15px; height: 15px; margin-left: 14px; fill: var(--ink); }
  .rule {
    position: absolute; left: 0; right: 0; top: 508px; height: 3px;
    background: var(--red);
  }
  .address-band {
    position: absolute; left: 0; right: 0; top: 512px; height: 53px;
    background: var(--navy);
    color: var(--band-text);
    font-size: 21px; letter-spacing: 0.6px;
    display: flex; align-items: center; justify-content: flex-end;
    padding-right: 58px;
  }
</style>
</head>
<body>
  <article class="card">
    <div class="agent-photo" role="img" aria-label="Portrait of the agent, smiling, in a navy suit and striped tie"></div>

    <div class="brand"><span class="brand-mark"></span>Meridian Real Estate</div>

    <div class="person">
      <div class="person-name">DANIEL REYES</div>
      <div class="person-role">Managing Director</div>
    </div>

    <ul class="contacts">
      <li>+852 2418 5690
        <svg viewBox="0 0 24 24" aria-hidden="true"><path d="M6.6 10.8a15.1 15.1 0 0 0 6.6 6.6l2.2-2.2c.3-.3.7-.4 1-.2 1.1.4 2.3.6 3.6.6.6 0 1 .4 1 1V20c0 .6-.4 1-1 1A17 17 0 0 1 3 4c0-.6.4-1 1-1h3.5c.6 0 1 .4 1 1 0 1.3.2 2.5.6 3.6.1.3 0 .7-.2 1z"/></svg>
      </li>
      <li>+852 2418 5691
        <svg viewBox="0 0 24 24" aria-hidden="true"><path d="M7 3h10v5H7zM4 9h16a2 2 0 0 1 2 2v6h-4v4H6v-4H2v-6a2 2 0 0 1 2-2zm4 7v3h8v-3z"/></svg>
      </li>
      <li>hello@meridianhomes.com
        <svg viewBox="0 0 24 24" aria-hidden="true"><path d="M2 5h20v14H2zm2 2v.5l8 5 8-5V7zm0 2.8V17h16V9.8l-8 5z"/></svg>
      </li>
      <li>www.meridianhomes.com
        <svg viewBox="0 0 24 24" aria-hidden="true"><path d="M12 2a10 10 0 1 0 0 20 10 10 0 0 0 0-20zm6.9 6h-3a15 15 0 0 0-1.3-3.9A8 8 0 0 1 18.9 8zM12 4c.8 1.2 1.5 2.5 1.9 4h-3.8c.4-1.5 1.1-2.8 1.9-4zM4.3 14a8 8 0 0 1 0-4h3.4a16 16 0 0 0 0 4zm.8 2h3a15 15 0 0 0 1.3 3.9A8 8 0 0 1 5.1 16zm3-8h-3a8 8 0 0 1 4.3-3.9A15 15 0 0 0 8.1 8zM12 20c-.8-1.2-1.5-2.5-1.9-4h3.8c-.4 1.5-1.1 2.8-1.9 4zm2.3-6H9.7a14 14 0 0 1 0-4h4.6a14 14 0 0 1 0 4zm.3 5.9a15 15 0 0 0 1.3-3.9h3a8 8 0 0 1-4.3 3.9zm1.7-5.9a16 16 0 0 0 0-4h3.4a8 8 0 0 1 0 4z"/></svg>
      </li>
    </ul>

    <div class="rule"></div>
    <div class="address-band">Via dei Tigli, 48. 12030 Cervasca (CN)</div>
  </article>
</body>
</html>
```